Fahrzeugbeschriftung für mittelständische Abbruch- und Schadstoffsanierungsfirma
Zielgruppe
Wir sind eine mittelständische Abbruch- und Schadstoffsanierungsfirma.
Aufgabenstellung
Unsere Fahrzeuge haben bereits Werbung, jedoch soll das Design für ein Halvorn Teska überarbeitet und modernisiert werden. Jedoch soll der Stil ähnlich bleiben.

```html
<!DOCTYPE html>
<html lang="de">
<head>
<meta charset="utf-8">
<title>Velmar Bauservice – Fahrzeugbeschriftung</title>
<link rel="stylesheet" href="https://fonts.googleapis.com/css2?family=Fira+Sans+Extra+Condensed:wght@500;600&family=Open+Sans:wght@400;600&display=swap">
<style>
  :root {
    --stage-top: #4d4e52;
    --stage-mid: #6b6c70;
    --stage-bottom: #505155;
    --band: #e6e7e9;
    --panel: #f7f7f7;
    --panel-edge: #d9d9d9;
    --glass: #1e1e20;
    --trim: #232325;
    --red: #d42a25;
    --ink: #1f1f1f;
    --white: #ffffff;
  }
  * { box-sizing: border-box; margin: 0; padding: 0; }
  html, body { width: 1068px; height: 1200px; overflow: hidden; }
  body {
    position: relative;
    font-family: "Fira Sans Extra Condensed", "Arial Narrow", sans-serif;
    background: linear-gradient(180deg, var(--stage-top) 0%, var(--stage-mid) 50%, var(--stage-bottom) 86%);
  }
  .vehicle-sheet { position: absolute; left: 0; top: 0; width: 1068px; height: 1032px; }
  .brand-band {
    position: absolute; left: 0; top: 1032px; width: 1068px; height: 168px;
    background: var(--band);
  }
  .abs { position: absolute; white-space: nowrap; }
  .brand-name {
    font-family: "Open Sans", sans-serif; font-weight: 600; color: var(--ink);
    letter-spacing: 0.5px;
  }
  .brand-square { display: inline-block; background: var(--red); vertical-align: middle; margin-right: 6px; }
  .brand-tagline {
    font-family: "Open Sans", sans-serif; font-weight: 400; color: var(--ink);
    letter-spacing: 0.6px; text-transform: uppercase;
  }
  .web { color: var(--red); font-weight: 600; }
  .service-tag {
    background: var(--red); color: var(--white); font-weight: 500;
    font-size: 12.5px; line-height: 15px; padding: 0 8px 0 13px;
  }
  .contact { color: var(--red); font-weight: 500; font-size: 10px; line-height: 12px; }
  .contact svg { width: 9px; height: 9px; vertical-align: -1px; margin-right: 6px; }
  .rear-services { color: var(--ink); font-weight: 500; font-size: 11px; line-height: 16px; }
  .rear-contact { color: var(--ink); font-weight: 500; font-size: 10px; line-height: 12.5px; }
  .rear-contact svg { width: 9px; height: 9px; vertical-align: -1px; margin-right: 6px; }
</style>
</head>
<body>

<section class="vehicle-sheet" aria-label="Fahrzeugbeschriftung Halvorn Teska">
  <svg width="1068" height="1032" viewBox="0 0 1068 1032">
    <!-- side view body -->
    <g class="side-body">
      <path d="M90 410 L88 352 Q92 300 150 270 L245 230 Q320 160 400 128 L530 122 L940 118 Q975 122 985 200 L995 330 L1000 395 Q998 410 985 412 L930 415 Q915 360 855 360 Q795 360 785 420 L300 430 Q290 362 225 362 Q165 362 155 420 Z" fill="var(--panel)"/>
      <path d="M270 255 Q320 170 380 142 L500 140 L495 250 Z" fill="var(--glass)"/>
      <path d="M90 410 L90 345 Q115 330 150 320 L160 345 Q150 380 155 420 Z" fill="var(--trim)"/>
      <path d="M930 415 Q925 350 990 320 L1000 395 Q998 410 985 412 Z" fill="var(--trim)"/>
      <!-- simple bands replacing brand shapes -->
      <path d="M320 405 L780 398 L780 420 L320 428 Z" fill="var(--trim)"/>
      <path d="M320 392 L780 386 L780 393 L320 399 Z" fill="var(--red)"/>
      <circle cx="225" cy="420" r="58" fill="var(--trim)"/>
      <circle cx="225" cy="420" r="44" fill="#b9b9bb"/>
      <circle cx="857" cy="418" r="58" fill="var(--trim)"/>
      <circle cx="857" cy="418" r="44" fill="#b9b9bb"/>
      <line x1="523" y1="128" x2="523" y2="428" stroke="var(--panel-edge)"/>
      <line x1="755" y1="125" x2="762" y2="405" stroke="var(--panel-edge)"/>
    </g>
    <!-- front view body -->
    <g class="front-body">
      <path d="M135 570 Q140 560 160 560 L395 560 Q412 560 418 572 L445 680 Q470 720 470 780 L468 900 Q466 915 450 915 L80 915 Q64 915 62 900 L60 780 Q60 720 85 680 Z" fill="var(--panel)"/>
      <path d="M145 575 L400 575 L425 662 L118 662 Z" fill="var(--glass)"/>
      <path d="M62 780 Q62 730 90 720 L440 720 Q470 730 468 780 L468 900 Q466 915 450 915 L80 915 Q64 915 62 900 Z" fill="var(--trim)"/>
      <rect x="150" y="735" width="240" height="70" rx="12" fill="#2d2d30"/>
    </g>
    <!-- rear view body -->
    <g class="rear-body">
      <path d="M640 560 Q645 550 665 550 L955 550 Q970 550 975 560 L1000 690 L1005 900 Q1004 925 985 925 L630 925 Q612 925 610 900 L612 690 Z" fill="var(--panel)"/>
      <path d="M610 770 L1005 770 L1005 900 Q1004 925 985 925 L630 925 Q612 925 610 900 Z" fill="var(--trim)"/>
      <path d="M636 772 L980 772 L978 842 Q975 855 960 855 L655 855 Q640 855 638 842 Z" fill="var(--panel)"/>
      <rect x="608" y="685" width="27" height="85" rx="6" fill="#9e1c1c"/>
      <rect x="976" y="685" width="27" height="85" rx="6" fill="#9e1c1c"/>
      <rect x="750" y="557" width="110" height="5" rx="2.5" fill="var(--red)"/>
      <rect x="746" y="781" width="116" height="22" rx="2" fill="var(--white)" stroke="#8a8a8a"/>
    </g>
  </svg>

  <!-- side: brand -->
  <div class="abs brand-name" style="left:596px;top:186px;font-size:15px;"><span class="brand-square" style="width:10px;height:10px;"></span>Velmar Bauservice</div>
  <div class="abs brand-tagline" style="left:598px;top:207px;font-size:4.6px;">Schadstoffsanierung | Abbruch | Entsorgung</div>
  <div class="abs web" style="left:555px;top:298px;font-size:24px;">www.velmar-bau.de</div>

  <!-- side: service tags -->
  <div class="abs service-tag" style="left:773px;top:201px;">Industrierückbau</div>
  <div class="abs service-tag" style="left:773px;top:219px;">Abbruch &amp; Entkernen</div>
  <div class="abs service-tag" style="left:773px;top:237px;">Entsorgung</div>
  <div class="abs service-tag" style="left:773px;top:255px;">Schadstoffsanierung, Asbest, KMF, PAK</div>

  <!-- side: contact -->
  <div class="abs contact" style="left:852px;top:292px;">
    <div><svg viewBox="0 0 10 10"><circle cx="5" cy="5" r="4.4" fill="none" stroke="currentColor" stroke-width="0.9"/><path d="M3.3 2.8 L4.2 2.6 L4.6 3.9 L4.1 4.3 Q4.6 5.4 5.7 5.9 L6.1 5.4 L7.4 5.8 L7.2 6.7 Q5 7 3.3 2.8 Z" fill="currentColor"/></svg>+49 (0) 150-27 384 19</div>
    <div><svg viewBox="0 0 10 10"><rect x="0.8" y="2" width="8.4" height="6" fill="none" stroke="currentColor" stroke-width="0.9"/><path d="M0.8 2 L5 5.4 L9.2 2" fill="none" stroke="currentColor" stroke-width="0.9"/></svg>kontakt@velmar-bau.de</div>
  </div>

  <!-- front: hood brand -->
  <div class="abs brand-name" style="left:222px;top:680px;font-size:10px;"><span class="brand-square" style="width:7px;height:7px;"></span>Velmar Bauservice</div>
  <div class="abs brand-tagline" style="left:224px;top:695px;font-size:3.4px;">Schadstoffsanierung | Abbruch | Entsorgung</div>

  <!-- rear: brand -->
  <div class="abs brand-name" style="left:758px;top:632px;font-size:15px;"><span class="brand-square" style="width:10px;height:10px;"></span>Velmar Bauservice</div>
  <div class="abs brand-tagline" style="left:760px;top:653px;font-size:4.6px;">Schadstoffsanierung | Abbruch | Entsorgung</div>

  <div class="abs rear-services" style="left:658px;top:692px;">
    <div>Schadstoffsanierung</div>
    <div>Abbruch &amp; Entkernen</div>
    <div>Industrierückbau</div>
    <div>Entsorgung</div>
  </div>
  <div class="abs rear-contact" style="left:852px;top:710px;">
    <div><svg viewBox="0 0 10 10"><circle cx="5" cy="5" r="4.4" fill="none" stroke="currentColor" stroke-width="0.9"/><path d="M3.3 2.8 L4.2 2.6 L4.6 3.9 L4.1 4.3 Q4.6 5.4 5.7 5.9 L6.1 5.4 L7.4 5.8 L7.2 6.7 Q5 7 3.3 2.8 Z" fill="currentColor"/></svg>+49 (0) 150-27 384 19</div>
    <div><svg viewBox="0 0 10 10"><rect x="0.8" y="2" width="8.4" height="6" fill="none" stroke="currentColor" stroke-width="0.9"/><path d="M0.8 2 L5 5.4 L9.2 2" fill="none" stroke="currentColor" stroke-width="0.9"/></svg>kontakt@velmar-bau.de</div>
  </div>
  <div class="abs web" style="left:737px;top:825px;font-size:22px;">www.velmar-bau.de</div>
</section>

<footer class="brand-band">
  <div class="abs brand-name" style="left:850px;top:100px;font-size:18px;"><span class="brand-square" style="width:12px;height:12px;"></span>Velmar Bauservice</div>
  <div class="abs brand-tagline" style="left:866px;top:126px;font-size:5.6px;">Schadstoffsanierung | Abbruch | Entsorgung</div>
</footer>

</body>
</html>
```